Education Certificate

We need a modern yet professional Certificate for those who successfully pass / complete our online Training course.

There are various courses but ONE certificate design required.

the certificate needs to look extremely professional and of value.

```html
<!DOCTYPE html>
<html lang="en">
<head>
<meta charset="utf-8">
<title>Certificate of Completion</title>
<link rel="stylesheet" href="https://fonts.googleapis.com/css2?family=Cinzel:wght@700;800&family=Poppins:wght@400;500&family=Pinyon+Script&display=swap">
<style>
  :root {
    --navy: #1b1756;
    --navy-deep: #14124a;
    --gold-dark: #b8862a;
    --gold: #d9a93a;
    --gold-light: #f3cf4a;
    --ribbon-red: #a3121b;
    --paper: #ffffff;
    --paper-shade: #f1f1f4;
    --ink: #1c1c24;
    --rule: #2c3a8c;
    --backdrop: #e6e6e8;
  }
  * { margin: 0; padding: 0; box-sizing: border-box; }
  html, body {
    width: 1200px; height: 880px; overflow: hidden;
    background: var(--backdrop);
  }
  .certificate {
    position: absolute; left: 50px; top: 92px;
    width: 1075px; height: 680px;
    transform: scale(1.0233); transform-origin: 0 0;
    background: var(--paper);
    box-shadow: 0 10px 30px rgba(0,0,0,.12);
    overflow: hidden;
    font-family: 'Poppins', sans-serif;
    color: var(--ink);
  }
  .certificate-art { position: absolute; inset: 0; }
  .brand {
    position: absolute; left: 455px; top: 74px;
    display: flex; align-items: center; gap: 8px;
  }
  .brand-mark { width: 22px; height: 22px; background: var(--navy); }
  .brand-name {
    font-weight: 500; font-size: 13px; letter-spacing: .5px;
    color: var(--navy); text-transform: uppercase;
  }
  .title {
    position: absolute; left: 0; width: 1070px; top: 140px;
    text-align: center;
    font-family: 'Cinzel', serif; font-weight: 800; font-size: 68px; line-height: 1;
    background: linear-gradient(90deg, var(--gold-dark), var(--gold-light) 50%, var(--gold-dark));
    -webkit-background-clip: text; background-clip: text; color: transparent;
  }
  .subtitle {
    position: absolute; left: 0; width: 1070px; top: 212px;
    display: flex; justify-content: center; align-items: center; gap: 10px;
    font-weight: 500; font-size: 30px; letter-spacing: 6px; line-height: 1;
  }
  .subtitle-flag { width: 16px; height: 20px; background: var(--gold-light); }
  .subtitle-flag.left { clip-path: polygon(0 0,100% 0,100% 100%,0 100%,45% 50%); }
  .subtitle-flag.right { clip-path: polygon(0 0,100% 0,55% 50%,100% 100%,0 100%); }
  .presented {
    position: absolute; left: 0; width: 1070px; top: 271px;
    text-align: center; font-size: 21px; letter-spacing: 6px; font-weight: 500;
  }
  .recipient {
    position: absolute; left: 255px; width: 560px; top: 300px; height: 96px;
    text-align: center; font-family: 'Pinyon Script', cursive; font-size: 84px; line-height: 96px;
    border-bottom: 1.5px solid var(--rule);
  }
  .field {
    position: absolute; display: flex; align-items: flex-end;
    font-weight: 500; font-size: 21px; letter-spacing: 1.5px; line-height: 1;
  }
  .field-line { flex: 1; border-bottom: 1.5px solid var(--rule); margin-left: 10px; margin-bottom: 3px; }
  .field.course { left: 118px; width: 815px; top: 428px; }
  .field.duration { left: 118px; width: 818px; top: 468px; }
  .field.date { left: 118px; width: 336px; top: 513px; }
  .field.date .field-line { margin-left: 14px; }
  .field.signature { left: 478px; width: 462px; top: 513px; }
  .award-text {
    position: absolute; left: 872px; top: 152px; width: 120px;
    text-align: center; color: var(--ink); line-height: 1;
  }
  .award-year { font-size: 25px; font-weight: 500; letter-spacing: -.5px; }
  .award-label { font-size: 16px; font-weight: 500; letter-spacing: 1px; margin-top: 1px; }
</style>
</head>
<body>
  <main class="certificate">
    <svg class="certificate-art" viewBox="0 0 1075 680" width="1075" height="680" aria-hidden="true">
      <defs>
        <linearGradient id="paperSheen" x1="0" y1="0" x2="1" y2="1">
          <stop offset="0" stop-color="#ffffff"/>
          <stop offset=".6" stop-color="#f4f4f6"/>
          <stop offset="1" stop-color="#ececf0"/>
        </linearGradient>
        <linearGradient id="goldStroke" x1="0" y1="0" x2="1" y2="0">
          <stop offset="0" stop-color="#b8862a"/>
          <stop offset=".5" stop-color="#f3cf4a"/>
          <stop offset="1" stop-color="#b8862a"/>
        </linearGradient>
        <linearGradient id="sealGold" x1="0" y1="0" x2="0" y2="1">
          <stop offset="0" stop-color="#f7d24a"/>
          <stop offset="1" stop-color="#c98f1c"/>
        </linearGradient>
      </defs>
      <rect class="inner-panel" x="45" y="33" width="980" height="612" fill="url(#paperSheen)"/>
      <path d="M45 500 C300 380 650 420 1025 300" fill="none" stroke="#e8e8ec" stroke-width="40" opacity=".6"/>
      <!-- top-left corner -->
      <polygon points="0,0 270,0 0,185" fill="var(--navy)"/>
      <polygon points="270,0 262,0 0,179 0,185" fill="url(#goldStroke)"/>
      <!-- bottom-right corner -->
      <polygon points="1075,493 1075,680 815,680" fill="var(--navy)"/>
      <polygon points="1075,493 1075,500 825,680 815,680" fill="url(#goldStroke)"/>
      <!-- ribbon and seal -->
      <rect x="880" y="0" width="95" height="140" fill="var(--navy)"/>
      <polygon points="848,160 880,160 880,190 848,190 856,175" fill="var(--ribbon-red)"/>
      <polygon points="985,160 1018,160 1010,175 1018,190 985,190" fill="var(--ribbon-red)"/>
      <polygon points="932,114 992,144 992,202 932,232 872,202 872,144" fill="#e7b93a" stroke="#fff5c8" stroke-width="2"/>
      <polygon points="932,124 982,149 982,197 932,222 882,197 882,149" fill="url(#sealGold)"/>
    </svg>

    <div class="brand">
      <span class="brand-mark"></span>
      <span class="brand-name">Northbridge Service Academy</span>
    </div>

    <div class="award-text">
      <div class="award-year">2024</div>
      <div class="award-label">AWARD</div>
    </div>

    <h1 class="title">CERTIFICATE</h1>
    <p class="subtitle"><span class="subtitle-flag left"></span>OF COMPLETION<span class="subtitle-flag right"></span></p>
    <p class="presented">PROUDLY PRESENTED TO</p>
    <p class="recipient">Daniel Carter</p>

    <div class="field course"><span>COURSE NAME</span><span class="field-line"></span></div>
    <div class="field duration"><span>DURATION</span><span class="field-line"></span></div>
    <div class="field date"><span>DATE</span><span class="field-line"></span></div>
    <div class="field signature"><span>SIGNATURE</span><span class="field-line"></span></div>
  </main>
</body>
</html>
```